Law Firm Business Card

This is a business card for a law firm that serves US military and veterans.

The card must have ONLY the following (we want an uncluttered look):

- Company logo (PNG, GIF, JPEG copies uploaded)
- A tagline reading: "a law firm for service members and veterans"
- My name and title: "Tobias Marlow" and "Attorney"
- My email: "tobias.marlow@brinmoorlegal.com"
- My number: "855-FIRM-ONE (347-6663)"

We are looking for a clean, simple layout with only the above information, likely printed on a bright white cotton stock. The font of our logo is DIN 1451, and the font used on our website is Helvetica Neue. The color of our logo is #336699, and we probably want the tagline in that color also, and my contact information in a dark grey. Please review our website at www.brinmoorlegal.com to ensure your card design complements our website style.

Thanks and we look forward to seeing your submissions.

A few notes:

- Two-sided submissions are ok
- Please don't add graphics (scales of justice, judges hammer, etc)

```html
<!DOCTYPE html>
<html lang="en">
<head>
<meta charset="utf-8">
<title>Brinmoor Legal — Business Card</title>
<link rel="stylesheet" href="https://fonts.googleapis.com/css2?family=Barlow+Condensed:wght@600&family=Arimo:wght@400;700&display=swap">
<style>
  :root {
    --brand-blue: #336699;
    --card-blue: #3b70a6;
    --paper: #ffffff;
    --backdrop: #e6e2de;
    --ink-light: #dde6ef;
    --ink-grey: #4a4a4a;
  }
  * { margin: 0; padding: 0; box-sizing: border-box; }
  html, body {
    width: 1200px;
    height: 848px;
    overflow: hidden;
    background: var(--backdrop);
  }
  .sheet {
    width: 1200px;
    height: 848px;
    display: flex;
    align-items: center;
    justify-content: center;
    gap: 48px;
  }
  .card {
    position: relative;
    width: 540px;
    height: 309px;
    overflow: hidden;
    box-shadow: 0 10px 28px rgba(0,0,0,0.18);
  }

  /* Front */
  .card--front { background: var(--paper); }
  .wordmark {
    position: absolute;
    left: 0;
    right: 0;
    top: 62px;
    text-align: center;
    font-family: "Barlow Condensed", "Arial Narrow", sans-serif;
    font-weight: 600;
    font-size: 58px;
    letter-spacing: 2px;
    line-height: 1;
    color: var(--brand-blue);
  }
  .tagline-band {
    position: absolute;
    left: 0;
    right: 0;
    top: 196px;
    height: 46px;
    background: var(--brand-blue);
    display: flex;
    align-items: center;
    padding-left: 30px;
  }
  .tagline {
    font-family: "Arimo", "Helvetica Neue", Helvetica, sans-serif;
    font-size: 19px;
    color: var(--paper);
    letter-spacing: 0.2px;
  }

  /* Back */
  .card--back { background: var(--card-blue); }
  .back-name {
    position: absolute;
    left: 30px;
    top: 28px;
    font-family: "Barlow Condensed", "Arial Narrow", sans-serif;
    font-weight: 600;
    font-size: 26px;
    letter-spacing: 1.5px;
    color: var(--paper);
  }
  .contact {
    position: absolute;
    left: 150px;
    top: 104px;
    font-family: "Arimo", "Helvetica Neue", Helvetica, sans-serif;
    color: var(--ink-light);
    font-size: 15px;
    line-height: 1.5;
  }
  .contact__name {
    font-weight: 700;
    font-size: 19px;
    color: var(--paper);
  }
  .contact__title { margin-bottom: 22px; }
</style>
</head>
<body>
  <main class="sheet">
    <section class="card card--front" aria-label="Card front">
      <div class="wordmark">BRINMOOR LEGAL</div>
      <div class="tagline-band">
        <p class="tagline">a law firm for service members and veterans</p>
      </div>
    </section>

    <section class="card card--back" aria-label="Card back">
      <div class="back-name">BRINMOOR LEGAL</div>
      <div class="contact">
        <p class="contact__name">Tobias Marlow</p>
        <p class="contact__title">Attorney</p>
        <p class="contact__email">tobias.marlow@brinmoorlegal.com</p>
        <p class="contact__phone">855-FIRM-ONE (347-6663)</p>
      </div>
    </section>
  </main>
</body>
</html>
```